Web design - holistic filmmaker

I need a design for my new website.

I am a holistic filmmaker, ie I make films for healers, alternative practitioners, spiritual people and institutions that offer training in this field.

The design should be noble, bright, convey the feeling of space and expanse and have some particularly beautiful color accents.

The structure is: start page, offer, references, about me, imprint.

As an idea for the start page, I thought that either I could introduce myself as a filmmaker and my offer, or we could start right on the start page with the references, ie photos and links to already realized projects.

If you want more information or an exchange, I'd love to hear from you. At the moment I just don't know how to describe it better.

The winner will then be asked to design a logo.

Target Market(s)

healers, alternative practitioners, spiritual people and institutions that offer training in this field

Industry/Entity Type

Film production

Number of Pages Required

3 page

```html
<!DOCTYPE html>
<html lang="en">
<head>
<meta charset="utf-8">
<title>Jonas Verhoek – Holistic Filmmaker</title>
<link rel="stylesheet" href="https://fonts.googleapis.com/css2?family=Josefin+Sans:wght@200;300;400;600;700&family=Poppins:wght@300;400;500;600&display=swap">
<style>
:root{
  --bg:#eaf4fd;
  --ink:#1d2a3c;
  --text:#4a5566;
  --muted:#6f7a88;
  --line:#c3cfdb;
  --blue:#3d8fe0;
  --blue-deep:#2479d6;
  --blue-light:#7cbcf6;
  --accent:#e9485a;
  --gold:#f5dc8a;
  --white:#ffffff;
}
*{margin:0;padding:0;box-sizing:border-box}
html,body{width:1200px;height:3548px;overflow:hidden}
body{background:var(--bg);font-family:"Poppins",sans-serif;color:var(--text);position:relative}
.abs{position:absolute}

/* header */
.site-header{position:absolute;left:0;top:0;width:1200px;height:90px;border-bottom:1px solid var(--line)}
.brand{left:231px;top:30px;font-family:"Josefin Sans",sans-serif;font-weight:300;font-size:24px;letter-spacing:6px;color:var(--ink);white-space:nowrap}
.main-nav{left:625px;top:37px;display:flex;gap:31px;font-size:11.5px;font-weight:500;color:var(--ink)}

/* hero */
.ornament{border-radius:50%;opacity:.55}
.ornament-gold{background:radial-gradient(circle,rgba(245,220,138,.55) 0%,rgba(245,220,138,.25) 45%,rgba(245,220,138,0) 70%)}
.ornament-pale{background:radial-gradient(circle,rgba(200,215,235,.7) 0%,rgba(200,215,235,.3) 45%,rgba(200,215,235,0) 70%)}
.hero-title{left:230px;top:232px;font-family:"Josefin Sans",sans-serif;font-weight:300;font-size:34px;color:var(--ink);white-space:nowrap}
.hero-text{left:231px;top:276px;width:330px;font-size:11.5px;line-height:21px;color:var(--text)}
.btn{display:inline-block;background:var(--accent);color:var(--white);font-size:12px;font-weight:500;border-radius:16px;text-align:center}
.hero-btn{left:231px;top:353px;width:150px;height:30px;line-height:30px}
.hero-portrait{left:682px;top:131px;width:296px;height:343px;background:linear-gradient(180deg,#c9c9c9 0%,#b89a86 45%,#e98a24 78%,#4a4a4e 100%);border-radius:46% 46% 0 0 / 36% 36% 0 0}
.hero-rule{left:0;top:474px;width:1200px;height:2px;background:var(--line)}

/* offers */
.section-title{font-family:"Josefin Sans",sans-serif;font-weight:300;letter-spacing:9px;color:var(--ink);white-space:nowrap}
.offers-title{left:0;width:1200px;top:525px;text-align:center;font-size:30px}
.offer{width:160px;text-align:center}
.offer-icon{width:108px;height:108px;margin:0 auto;border-radius:50%;background:radial-gradient(circle at 40% 35%,#6ab2f5,#2a82dd);box-shadow:0 8px 18px rgba(42,130,221,.35);display:flex;align-items:center;justify-content:center}
.offer-label{margin-top:16px;font-size:12px;letter-spacing:2.5px;color:var(--muted)}
.offers-rule{left:322px;top:755px;width:556px;height:1px;background:var(--muted);opacity:.6}
.offers-copy{left:318px;top:787px;width:564px;text-align:center;font-size:11px;line-height:18.6px;color:var(--text)}
.offers-copy p{margin-bottom:19px}

/* about */
.about{left:0;top:1098px;width:1200px;height:602px;background:linear-gradient(100deg,#7ebdf6 0%,#4a9ae8 45%,#2380d8 100%);overflow:hidden}
.about-arc{border:2px solid rgba(40,120,210,.55);border-radius:50%}
.about-halo{left:208px;top:1200px;width:300px;height:300px;border-radius:50%;background:#85c0f5}
.about-portrait{left:225px;top:1217px;width:266px;height:266px;border-radius:50%;background:linear-gradient(160deg,#5b6b55 0%,#b9a99a 45%,#2c2c30 100%)}
.about-name{left:208px;width:300px;top:1505px;text-align:center;font-family:"Josefin Sans",sans-serif;font-weight:300;font-size:17px;letter-spacing:5px;color:var(--white);white-space:nowrap}
.socials{display:flex;gap:12px}
.about-socials{left:305px;top:1537px}
.social-dot{width:26px;height:26px;border-radius:50%;border:2px solid var(--white);background:rgba(255,255,255,.25)}
.about-title{left:532px;top:1144px;font-size:38px;color:var(--white)}
.about-copy{left:532px;top:1194px;width:450px;font-size:10.6px;line-height:15px;color:var(--white)}
.about-copy p{margin-bottom:15px}
.about-flower{left:1018px;top:1213px;width:240px;height:344px;border-radius:50%;background:radial-gradient(circle at 40% 50%,#f6d54a 0%,#e8482b 30%,#28a24b 55%,#1e6fd0 75%,rgba(30,111,208,0) 80%)}

/* works */
.works-title{left:0;width:1200px;top:1765px;text-align:center;font-size:38px}
.rule{left:232px;width:737px;height:1px;background:var(--line)}
.work-thumb{width:313px;height:171px;border:2px solid var(--blue);border-radius:4px}
.thumb-a{background:linear-gradient(90deg,#4b3a34 0%,#b98a78 45%,#c24f84 62%,#d8d3cb 100%)}
.thumb-b{background:linear-gradient(90deg,#3e4a46 0%,#8b8d86 40%,#d9b7a4 60%,#c8424d 100%)}
.thumb-c{background:linear-gradient(160deg,#5a8fd6 0%,#9fc3ee 50%,#5a4740 100%)}
.work-name{font-family:"Josefin Sans",sans-serif;font-weight:600;font-size:27px;letter-spacing:2px;color:var(--ink)}
.work-text{width:245px;font-size:11px;line-height:19px;color:var(--text)}
.more{font-size:11px;font-weight:600;color:var(--accent)}
.portfolio-link{left:0;width:1200px;top:2641px;text-align:center;font-size:11px;font-weight:600;letter-spacing:1.5px;color:var(--accent)}

/* testimonials */
.testimonials{left:0;top:2720px;width:1200px;height:499px;background:linear-gradient(180deg,#3189de 0%,#60a9f0 60%,#7bbcf6 100%);overflow:hidden}
.testi-title{left:0;width:1200px;top:2772px;text-align:center;font-size:38px;color:var(--white)}
.card{width:215px;height:287px;top:2859px;border-radius:8px;background:linear-gradient(180deg,#ffffff 0%,#dcecfc 100%);box-shadow:0 6px 18px rgba(20,70,140,.2);padding:56px 20px 0 20px}
.card-head{display:flex;align-items:center;gap:10px;margin-bottom:26px}
.avatar{width:42px;height:42px;border-radius:50%;background:linear-gradient(160deg,#c8a98f,#3a3a3a)}
.card-name{font-size:11px;color:var(--muted)}
.stars{font-size:13px;letter-spacing:1px;color:var(--ink)}
.card-text{font-size:11px;line-height:18.5px;color:var(--muted)}
.arrow{top:2988px}

/* contact band */
.cta{left:0;top:3219px;width:1200px;height:232px;background:linear-gradient(90deg,#b7b0ab 0%,#e6dcd5 35%,#d6c0ae 60%,#a99a90 100%)}
.cta-veil{left:0;top:3219px;width:1200px;height:232px;background:rgba(234,244,253,.45)}
.cta-title{left:0;width:1200px;top:3276px;text-align:center;font-family:"Josefin Sans",sans-serif;font-weight:700;font-size:28px;color:var(--ink)}
.cta-sub{left:0;width:1200px;top:3318px;text-align:center;font-size:13px;color:var(--ink)}
.cta-btn{left:520px;top:3357px;width:156px;height:32px;line-height:32px;font-size:13px}

/* footer */
.footer-brand{left:226px;top:3486px;font-family:"Josefin Sans",sans-serif;font-weight:300;font-size:16px;letter-spacing:4px;color:var(--ink);white-space:nowrap}
.footer-tag{left:250px;top:3509px;font-size:8px;font-weight:600;color:var(--ink)}
.footer-nav{left:460px;top:3494px;display:flex;gap:33px;font-size:11px;color:var(--ink)}
.footer-socials{left:866px;top:3487px}
.footer-socials .social-dot{border:none;background:var(--ink)}
</style>
</head>
<body>

<header class="site-header">
  <div class="abs brand">JONAS VERHOEK</div>
  <nav class="abs main-nav"><span>Home</span><span>Services</span><span>Portfolio</span><span>References</span><span>Contact</span></nav>
</header>

<div class="abs ornament ornament-gold" style="left:-170px;top:60px;width:430px;height:520px" role="img" aria-label="Faint golden mandala ornament"></div>

<section class="hero">
  <h1 class="abs hero-title">Films for Open Hearts</h1>
  <p class="abs hero-text">I am a holistic filmmaker, documenting advertising films that are close to the people. The production of your film is always also a journey to yourself.</p>
  <a class="abs btn hero-btn">Get In Touch</a>
  <div class="abs hero-portrait" role="img" aria-label="Portrait of the filmmaker in an orange shirt and grey jacket"></div>
  <div class="abs hero-rule"></div>
</section>

<section class="offers">
  <h2 class="abs section-title offers-title">MY OFFERS</h2>
  <div class="abs offer" style="left:347px;top:587px">
    <div class="offer-icon"><svg width="52" height="52" viewBox="0 0 52 52" fill="none" stroke="#fff" stroke-width="2"><circle cx="20" cy="14" r="6"/><circle cx="32" cy="15" r="5"/><rect x="10" y="22" width="26" height="16" rx="2"/><path d="M36 27l8-4v14l-8-4"/><circle cx="23" cy="30" r="4"/></svg></div>
    <div class="offer-label">DIRECTING</div>
  </div>
  <div class="abs offer" style="left:520px;top:587px">
    <div class="offer-icon"><svg width="52" height="52" viewBox="0 0 52 52" fill="none" stroke="#fff" stroke-width="2"><rect x="10" y="12" width="28" height="22" rx="3"/><path d="M21 18l8 5-8 5z"/><circle cx="34" cy="36" r="3"/><circle cx="40" cy="40" r="3"/><path d="M30 30l12 12M42 30L30 42"/></svg></div>
    <div class="offer-label">EDITING</div>
  </div>
  <div class="abs offer" style="left:693px;top:587px">
    <div class="offer-icon"><svg width="52" height="52" viewBox="0 0 52 52" fill="none" stroke="#fff" stroke-width="2"><circle cx="26" cy="13" r="5"/><path d="M26 18v6"/><circle cx="16" cy="28" r="4"/><circle cx="36" cy="28" r="4"/><path d="M9 42c0-5 3-8 7-8s7 3 7 8M29 42c0-5 3-8 7-8s7 3 7 8"/></svg></div>
    <div class="offer-label">CONSULTANCY</div>
  </div>
  <div class="abs offers-rule"></div>
  <div class="abs offers-copy">
    <p>Making a movie is always a journey to yourself. With simple means and without special effects, I accompany you on the way to portraying your essence. A documentary commercial film close to the people. Open Hearts Films is aimed at all people and institutions whose striving for truthfulness is the driving force behind their actions.</p>
    <p>High-quality image design and the informative and comprehensible communication of complex issues are the passion and basis of my image films and company presentations.</p>
    <p>As a full-service provider, I offer everything from one source, from consulting and conception to the finished film.</p>
    <p>Advertising films, image films, company presentations, interviews, documentaries, event recordings, also with several cameras or live streams - I am supported by a long-standing and excellent network of freelancers, creatives and technical service providers.</p>
  </div>
</section>

<section>
  <div class="abs about">
    <div class="abs about-arc" style="left:-60px;top:285px;width:480px;height:480px"></div>
  </div>
  <div class="abs about-halo"></div>
  <div class="abs about-portrait" role="img" aria-label="Circular portrait of the filmmaker holding a camera"></div>
  <div class="abs about-name">JONAS VERHOEK</div>
  <div class="abs socials about-socials">
    <span class="social-dot" role="img" aria-label="Professional network profile"></span>
    <span class="social-dot" role="img" aria-label="Social profile"></span>
    <span class="social-dot" role="img" aria-label="Photo profile"></span>
  </div>
  <h2 class="abs section-title about-title">ABOUT ME</h2>
  <div class="abs about-copy">
    <p>My name is Jonas and I make films - with curiosity and a whole heart. I am a holistic filmmaker.</p>
    <p>Around the turn of the millennium, I stood at a crossroads between natural healing and the world of cinema. Professionally, I chose film at that time, but the spiritual and my passion for gentle healing methods have stayed with me almost as strongly ever since.</p>
    <p>My cinematic path took me step by step from cable assistant to cameraman, director and producer. It began with assisting camera crews for the news agency NVX. In the years that followed, I worked in many roles on television productions at home and abroad, on cinema and documentary films, commercials and live productions.</p>
    <p>Working in the documentary field shaped my career the most. The insights into the varied life stories of the people involved and the cinematic way of storytelling fascinated me deeply - and I still follow this approach today.</p>
    <p>The combination of my cinematic aspirations with my holistic world view and my deep empathy leads me almost naturally to the core of my clients and their activities. That is why I also call my films documentary advertising films close to the people.</p>
    <p>Perhaps the most formative influence on my work as a filmmaker was my training in systemic coaching at the Inhaven Institute in Leiden. My empathy and the balance between pacing and leading, i.e. following and guiding people in their story, found their fundamental orientation there.</p>
  </div>
  <div class="abs about-flower" role="img" aria-label="Close-up of a multicoloured flower"></div>
</section>

<section>
  <div class="abs ornament ornament-gold" style="left:-150px;top:1760px;width:360px;height:420px" role="img" aria-label="Faint golden mandala ornament"></div>
  <div class="abs ornament ornament-pale" style="left:990px;top:2470px;width:300px;height:300px" role="img" aria-label="Faint pale mandala ornament"></div>
  <h2 class="abs section-title works-title">LATEST WORKS</h2>
  <div class="abs rule" style="top:1841px"></div>

  <div class="abs work-thumb thumb-a" style="left:269px;top:1885px" role="img" aria-label="Video still of a woman presenting in a bright room"></div>
  <h3 class="abs work-name" style="left:631px;top:1905px">Lumora</h3>
  <p class="abs work-text" style="left:631px;top:1942px">Con sectetur adipiscing elit, sed do eius mod tempor incididunt ut labore et dolore magna aliqua. Quis ipsum suspendisse</p>
  <a class="abs more" style="left:631px;top:2006px">Learn More &gt;&gt;</a>
  <div class="abs rule" style="top:2099px"></div>

  <h3 class="abs work-name" style="left:299px;top:2160px">Inhaven</h3>
  <p class="abs work-text" style="left:299px;top:2197px">Lorem ipsum dolor sit amet, con sectetur adipiscing elit, sed do eiusmod tempor incididunt ut labore et dolore magna</p>
  <a class="abs more" style="left:299px;top:2264px">Learn More &gt;&gt;</a>
  <div class="abs work-thumb thumb-b" style="left:620px;top:2141px" role="img" aria-label="Video still of two people in a seminar session"></div>
  <div class="abs rule" style="top:2354px"></div>

  <div class="abs work-thumb thumb-c" style="left:269px;top:2398px" role="img" aria-label="Video still of a woman in front of a television tower"></div>
  <h3 class="abs work-name" style="left:628px;top:2416px">SOL-TARA</h3>
  <p class="abs work-text" style="left:631px;top:2452px">Lorem ipsum dolor sit amet, con sectetur adipiscing elit, sed do eiusmod tempor incididunt ut labore et dolore magna</p>
  <a class="abs more" style="left:631px;top:2519px">Learn More &gt;&gt;</a>
  <div class="abs rule" style="top:2611px"></div>
  <a class="abs portfolio-link">&lt; VIEW FULL PORTFOLIO &gt;</a>
</section>

<section>
  <div class="abs testimonials">
    <div class="abs ornament ornament-gold" style="left:-140px;top:90px;width:330px;height:360px;opacity:.7" role="img" aria-label="Faint golden mandala ornament"></div>
  </div>
  <h2 class="abs section-title testi-title">CLIENT TESTIMONIALS</h2>
  <svg class="abs arrow" style="left:248px" width="14" height="30" viewBox="0 0 14 30" fill="none" stroke="rgba(255,255,255,.4)" stroke-width="2"><path d="M12 2L2 15l10 13"/></svg>
  <svg class="abs arrow" style="left:293px" width="14" height="30" viewBox="0 0 14 30" fill="none" stroke="#fff" stroke-width="2"><path d="M2 2l10 13L2 28"/></svg>

  <div class="abs card" style="left:353px">
    <div class="card-head"><span class="avatar" role="img" aria-label="Client photo"></span><div><div class="card-name">Amber</div><div class="stars">★★★★★</div></div></div>
    <p class="card-text">Lorem ipsum dolor sit amet, consectetur adipiscing elit, sed do eiusmod tempor incididunt ut labore.</p>
  </div>
  <div class="abs card" style="left:593px">
    <div class="card-head"><span class="avatar" role="img" aria-label="Client photo"></span><div><div class="card-name">James</div><div class="stars">★★★★★</div></div></div>
    <p class="card-text">Eli sed do eiusmod tempor incididunt ut labore et dolore magna aliqua.</p>
  </div>
  <div class="abs card" style="left:832px">
    <div class="card-head"><span class="avatar" role="img" aria-label="Client photo"></span><div><div class="card-name">Hillary</div><div class="stars">★★★★★</div></div></div>
    <p class="card-text">Adipiscing elit, sed do eiusmod tempor incididunt ut labore et dolore magna aliqua.</p>
  </div>
</section>

<section>
  <div class="abs cta" role="img" aria-label="Soft faded photo of camera operators filming a smiling man"></div>
  <div class="abs cta-veil"></div>
  <h2 class="abs cta-title">WORK WITH ME</h2>
  <p class="abs cta-sub">Get in touch with me for your project for more details</p>
  <a class="abs btn cta-btn">Get In Touch</a>
</section>

<footer>
  <div class="abs footer-brand">JONAS VERHOEK</div>
  <div class="abs footer-tag">filmmaker &amp; director</div>
  <nav class="abs footer-nav"><span>Services</span><span>Portfolio</span><span>References</span><span>Contact</span></nav>
  <div class="abs socials footer-socials">
    <span class="social-dot" role="img" aria-label="Professional network profile"></span>
    <span class="social-dot" role="img" aria-label="Social profile"></span>
    <span class="social-dot" role="img" aria-label="Photo profile"></span>
  </div>
</footer>

</body>
</html>
```